PAX

We need to design a power point presentation that can englobe all our company products.

This presentation has to have all the required to be used as template for future presentations.

We focus on prodcut developing for supermarkets, ( we help them with their own brand products ex. Sunny Harvest, TK, etc.)
Also we are on the marine industry, we develop ships and oil rigs for the Oil and deep water market.

Target Market(s)

Oil Companies
Supermarket companies
Retail Companies

Industry/Entity Type

It Company

Requirements
Must have
• Our Logo and company colors
Nice to have
• Something describing globalization.
Should not have
• Orange color

```html
<!DOCTYPE html>
<html lang="en">
<head>
<meta charset="utf-8">
<title>PAX Presentation Template</title>
<link rel="stylesheet" href="https://fonts.googleapis.com/css2?family=Exo+2:wght@700&family=Open+Sans:wght@400;600&display=swap">
<style>
  :root {
    --brand-blue: #1a7fd4;
    --title-blue: #1d8ad8;
    --body-grey: #6a6a6a;
    --strong-grey: #4a4a4a;
    --header-white: #ffffff;
    --canvas-grey: #eeeff0;
    --rule-grey: #d6d6d6;
    --footer-lime: #b4fb52;
    --footer-rule: #3c6a2a;
    --footer-text: #2e5120;
    --mark-green: #8cc63f;
  }
  * { margin: 0; padding: 0; box-sizing: border-box; }
  html, body { width: 1200px; height: 900px; overflow: hidden; }
  body { font-family: "Open Sans", Arial, sans-serif; background: var(--canvas-grey); }

  .slide { position: relative; width: 1200px; height: 900px; overflow: hidden;
    background: linear-gradient(180deg, #f6f6f6 0%, #eceded 100%); }

  .backdrop { position: absolute; left: 0; top: 105px; width: 1200px; height: 744px;
    background: radial-gradient(ellipse 700px 520px at 180px 260px, #dcdde0 0%, rgba(230,231,233,0.6) 45%, rgba(240,240,240,0) 80%),
                radial-gradient(ellipse 600px 400px at 900px 200px, #e8e9ea 0%, rgba(240,240,240,0) 75%); }

  .slide-header { position: absolute; left: 0; top: 0; width: 1200px; height: 106px;
    background: linear-gradient(180deg, #ffffff 0%, #f7f7f7 100%);
    border-bottom: 2px solid var(--rule-grey); }
  .slide-title { position: absolute; left: 60px; top: 30px; font-family: "Exo 2", Arial, sans-serif;
    font-weight: 700; font-size: 40px; letter-spacing: 0.5px; color: var(--brand-blue); }

  .brand-tab { position: absolute; left: 1038px; top: -2px; width: 124px; height: 174px;
    background: #ffffff; border: 2px solid #d9d9d9; border-top: none; border-radius: 0 0 62px 62px;
    display: flex; align-items: center; justify-content: center; gap: 8px; }
  .brand-dot { width: 18px; height: 18px; border-radius: 50%; background: var(--mark-green); }
  .brand-name { font-family: "Open Sans", Arial, sans-serif; font-weight: 600; font-size: 30px; color: var(--brand-blue); }

  .column { position: absolute; top: 175px; width: 480px; }
  .column-left { left: 64px; }
  .column-right { left: 636px; }
  .column h2 { font-weight: 400; font-size: 33px; color: var(--title-blue); line-height: 44px; margin-bottom: 13px; }
  .column p { font-size: 20.5px; line-height: 39px; color: var(--body-grey); text-align: justify; margin-bottom: 39px; }
  .column strong { font-weight: 600; color: var(--strong-grey); }

  .column-divider { position: absolute; left: 595px; top: 210px; width: 1px; height: 495px;
    background: linear-gradient(180deg, rgba(200,200,200,0) 0%, #d4d4d4 30%, #d4d4d4 70%, rgba(200,200,200,0) 100%); }

  .slide-footer { position: absolute; left: 0; top: 848px; width: 1200px; height: 52px;
    background: var(--footer-lime); border-top: 2px solid var(--footer-rule);
    display: flex; align-items: center; justify-content: space-between; padding: 0 12px 0 34px;
    font-weight: 600; font-size: 19.5px; color: var(--footer-text); }
</style>
</head>
<body>
<div class="slide">
  <div class="backdrop" role="img" aria-label="Soft grey halftone dot pattern suggesting a globe"></div>

  <header class="slide-header">
    <h1 class="slide-title">Persentation Title Here</h1>
  </header>

  <div class="brand-tab">
    <span class="brand-dot"></span>
    <span class="brand-name">PAX</span>
  </div>

  <section class="column column-left">
    <h2>Content Title Here</h2>
    <p><strong>Lorem ipsum dolor sit ipsum</strong> Lorem ipsum dolor sit ipsum Lorem ipsum Lorem ipsum dolor sit ipsum Lorem ipsum dolor sit ipsum Lorem ipsum.</p>
    <p><strong>Lorem ipsum dolor sit</strong> ipsum Lorem ipsum dolor sit ipsum Lorem ipsum Lorem ipsum dolor sit ipsum Lorem ipsum dolor sit ipsum Lorem ipsum.</p>
    <p>Lorem ipsum dolor sit ipsum Lorem ipsum dolor sit ipsum Lorem ipsum Lorem ipsum dolor sit ipsum Lorem ipsum dolor sit ipsum Lorem ipsum.</p>
  </section>

  <div class="column-divider"></div>

  <section class="column column-right">
    <h2>Content Title Here</h2>
    <p>Lorem ipsum dolor sit ipsum Lorem ipsum dolor sit ipsum Lorem ipsum Lorem ipsum dolor sit ipsum Lorem ipsum dolor sit ipsum Lorem ipsum.</p>
    <p>Lorem ipsum dolor sit ipsum Lorem ipsum dolor sit ipsum Lorem ipsum Lorem ipsum dolor sit ipsum Lorem ipsum dolor sit ipsum Lorem ipsum.</p>
    <p>Lorem ipsum dolor sit ipsum Lorem ipsum dolor sit ipsum Lorem ipsum Lorem ipsum dolor sit ipsum Lorem ipsum dolor sit ipsum Lorem ipsum.</p>
  </section>

  <footer class="slide-footer">
    <span class="page-number">Page : 01</span>
    <span class="copyright">Copyright Text here</span>
  </footer>
</div>
</body>
</html>
```